Recruitment of Trellan Staffing for the UK market

I want a website for the UK market to attract businesses and companies to come to us for Philipine labour. We want an information site that gives all information on what we do and how we can recruit Philippine labour.
This is a recruitment site for companies to contact us with their requirements for skilled workers coming from the Philipines over to the UK to work.

Target Market(s)

Uk Companies and businesses who want Philipine skilled workers

Industry/Entity Type

REcruitment

Coding

Number of Pages Required

5+ page

Font styles to use
Sans Serif

Colors
0054AA
0677BA
7BADD7
CADEEF
E8F1F8
0094D4
00A9DD
6FCCEA
C7EBF8
E9F6FB
EE7325
F08F49
F5BC92
FAE3D3
FDF4ED
EB3D1F
EC4F4E
F09395
F8D3D4
FCEDEE

Requirements
Must have
• Look professional and corperate with drop down menus for Home ,about, services,articles. training , contact us
Nice to have
• Look at Velmora recruitment- https://velmorarecruitment.example.co.uk/. This is my current site - https://www.trellanstaffing.example.com/
Should not have
• Cartoons or silly pictures , needs to be corperate looking

```html
<!DOCTYPE html>
<html lang="en">
<head>
<meta charset="utf-8">
<title>Trellan Staffing – Skilled Philippine Workers for UK Companies</title>
<link rel="stylesheet" href="https://fonts.googleapis.com/css2?family=Poppins:wght@400;500;600&family=Montserrat:wght@700&family=Oswald:wght@500&display=swap">
<style>
:root{
  --orange:#EE7325;
  --orange-soft:#FAE3D3;
  --cream:#FDF4ED;
  --red:#EB3D1F;
  --brand:#8B1E22;
  --ink:#1a1a1a;
  --text:#333;
  --pale-blue:#E8F1F8;
  --blue-soft:#CADEEF;
  --blue-line:#7BADD7;
  --navy:#0B1A38;
}
*{box-sizing:border-box;margin:0;padding:0}
html,body{width:1200px;height:4501px;overflow:hidden}
body{position:relative;font-family:"Poppins",sans-serif;color:var(--text);background:#fff}
.abs{position:absolute}
.ph{position:absolute}
h2.section-title{font-family:"Montserrat",sans-serif;font-weight:700;font-size:33px;letter-spacing:1px;color:var(--ink)}
.rule{width:42px;height:3px;background:var(--blue-soft);border-radius:2px}
.btn{display:inline-block;background:var(--orange);color:#fff;font-size:13px;padding:9px 20px;text-decoration:none}

/* header */
.site-header{top:0;left:0;width:1200px;height:75px;background:#fff;box-shadow:0 1px 4px rgba(0,0,0,.08);z-index:2}
.logo{left:161px;top:22px;font-family:"Poppins",sans-serif;font-weight:600;font-size:24px;color:var(--brand)}
.head-contact{top:28px;font-size:13px;color:#555;display:flex;align-items:center;gap:6px}
.menu-btn{left:996px;top:18px;width:42px;height:40px;background:var(--red);display:flex;align-items:center;justify-content:center}

/* hero */
.hero{top:75px;left:0;width:1200px;height:589px;background:linear-gradient(100deg,#2c3440 0%,#5b6470 45%,#3b4552 100%)}
.hero h1{position:absolute;left:161px;top:305px;font-family:"Oswald",sans-serif;font-weight:500;font-size:38px;line-height:49px;color:#fff}
.hero h1 span{color:var(--red)}
.form-card{left:687px;top:257px;width:353px;height:463px;background:#fff;box-shadow:0 6px 24px rgba(0,0,0,.12);z-index:2}
.form-card h3{text-align:center;margin-top:40px;font-family:"Oswald",sans-serif;font-weight:500;font-size:30px;color:var(--red)}
.field{position:absolute;left:32px;width:290px;height:38px;border:1px solid #aaa;font-size:12px;color:#666;padding:10px 12px 0 34px}
.field svg{position:absolute;left:14px;top:12px}
.form-card .send{position:absolute;left:107px;top:375px;background:var(--red);color:#fff;font-size:13px;padding:9px 20px}

/* about */
.centered{left:0;width:1200px;text-align:center}
.intro{font-size:13.5px;line-height:24px;color:#333}
.contact-strip{left:161px;top:956px;width:879px;height:69px;background:var(--cream)}
.strip-label{position:absolute;left:0;top:0;width:222px;height:69px;background:var(--orange);color:#fff;font-family:"Montserrat",sans-serif;font-weight:700;font-size:22px;display:flex;align-items:center;justify-content:center}
.strip-item{position:absolute;font-size:13px;line-height:22px;color:#222;display:flex;gap:10px}
.role-card{top:1083px;width:203px;height:301px;border-radius:4px;overflow:hidden}
.role-card span{position:absolute;bottom:16px;left:0;width:100%;text-align:center;color:#fff;font-size:14px;letter-spacing:.5px}

/* what we do */
.band{top:2006px;left:0;width:1200px;height:536px;background:var(--pale-blue)}
.body-copy{font-size:13.5px;line-height:24.5px;color:#333}

/* panels */
.panel{top:3087px;width:600px;height:468px;text-align:center}
.panel p{font-size:13.5px;line-height:30px;color:#333;margin:0 auto}

/* service cards */
.svc{top:3711px;width:270px;height:298px;background:var(--cream);border-radius:8px;text-align:center}
.svc.active{background:var(--orange);color:#fff}
.svc h4{margin-top:82px;font-size:15px;font-weight:500;letter-spacing:.5px;color:#111}
.svc p{margin:26px auto 0;width:230px;font-size:13px;line-height:22px;color:#333}
.svc.active h4,.svc.active p{color:#fff}
.svc .more{position:absolute;left:77px;top:225px;width:116px;height:36px;line-height:36px;background:var(--orange);color:#fff;font-size:13px}
.svc.active .more{background:#fff;color:#222}
.svc-icon{position:absolute;top:-60px;left:50%;margin-left:-56px;width:112px;height:112px;border-radius:50%;background:var(--orange);border:8px solid var(--orange-soft);display:flex;align-items:center;justify-content:center}

/* footer */
.footer{top:4114px;left:0;width:1200px;height:387px;background:var(--navy);color:#fff}
.footer h5{position:absolute;font-size:15px;font-weight:600;letter-spacing:.5px}
.footer .link{position:absolute;font-size:13px}
.footer .fline{position:absolute;font-size:13px;line-height:20px;display:flex;gap:10px}
.social{position:absolute;top:175px;width:28px;height:28px;border-radius:50%;background:#1e6fd1}
.copy{position:absolute;top:350px;left:0;width:1200px;text-align:center;font-size:13px}
</style>
</head>
<body>

<header class="site-header abs">
  <div class="logo abs">Trellan Staffing</div>
  <div class="head-contact abs" style="left:606px">
    <svg width="16" height="16" viewBox="0 0 24 24"><path d="M6.6 10.8a15 15 0 0 0 6.6 6.6l2.2-2.2a1 1 0 0 1 1-.25 11.4 11.4 0 0 0 3.6.57 1 1 0 0 1 1 1V20a1 1 0 0 1-1 1A17 17 0 0 1 3 4a1 1 0 0 1 1-1h3.5a1 1 0 0 1 1 1 11.4 11.4 0 0 0 .57 3.6 1 1 0 0 1-.25 1z" fill="none" stroke="#EB3D1F" stroke-width="1.8"/></svg>
    07700900418
  </div>
  <div class="head-contact abs" style="left:750px">
    <svg width="18" height="14" viewBox="0 0 18 14"><rect x="1" y="1" width="16" height="12" fill="none" stroke="#EB3D1F" stroke-width="1.6"/><path d="M1 1l8 7 8-7" fill="none" stroke="#EB3D1F" stroke-width="1.6"/></svg>
    sales@trellanstaffing.example.com
  </div>
  <div class="menu-btn abs">
    <svg width="18" height="14" viewBox="0 0 18 14"><path d="M1 2h16M4 7h10M7 12h4" stroke="#fff" stroke-width="2"/></svg>
  </div>
</header>

<section class="hero abs" role="img" aria-label="Engineer in a hard hat and a supervisor in a white hard hat reviewing plans in a factory">
  <h1>Recruiting and Placing Skilled<br>Philippine Workers into<br><span>UK Companies</span></h1>
</section>

<form class="form-card abs">
  <h3>Contact Us Today</h3>
  <div class="field" style="top:120px"><svg width="10" height="11" viewBox="0 0 10 11"><circle cx="5" cy="3" r="2.6" fill="#444"/><path d="M0 11a5 4.5 0 0 1 10 0z" fill="#444"/></svg>Name</div>
  <div class="field" style="top:165px"><svg width="11" height="9" viewBox="0 0 11 9"><rect width="11" height="9" fill="#444"/><path d="M0 0l5.5 4.5L11 0" stroke="#fff" fill="none"/></svg>Email</div>
  <div class="field" style="top:210px"><svg width="10" height="10" viewBox="0 0 24 24"><path d="M6.6 10.8a15 15 0 0 0 6.6 6.6l2.2-2.2a1 1 0 0 1 1-.25 11.4 11.4 0 0 0 3.6.57 1 1 0 0 1 1 1V20a1 1 0 0 1-1 1A17 17 0 0 1 3 4a1 1 0 0 1 1-1h3.5a1 1 0 0 1 1 1 11.4 11.4 0 0 0 .57 3.6 1 1 0 0 1-.25 1z" fill="#444"/></svg>Phone</div>
  <div class="field" style="top:256px;height:98px"><svg width="10" height="9" viewBox="0 0 10 9"><path d="M0 1h10M0 4.5h10M0 8h10" stroke="#444" stroke-width="1.6"/></svg>Message</div>
  <div class="send">Send Message</div>
</form>

<h2 class="section-title abs centered" style="top:796px">WHAT THE BUSINESS IS ABOUT</h2>
<div class="rule abs" style="left:579px;top:852px"></div>
<p class="intro abs centered" style="top:867px">We source skilled workers directly from the Philippines to work in the UK. With offices , training locations<br>and specialist recruiters we can find the highest quality individuals to add value and resources to any UK<br>buisness. We delivery quality based on vast experience over a number of years.</p>

<div class="contact-strip abs">
  <div class="strip-label">Contact Details</div>
  <div class="strip-item" style="left:245px;top:12px">
    <svg width="14" height="18" viewBox="0 0 14 18" style="margin-top:3px"><path d="M7 0a7 7 0 0 0-7 7c0 5 7 11 7 11s7-6 7-11a7 7 0 0 0-7-7z" fill="#EE7325"/><circle cx="7" cy="7" r="2.6" fill="#fff"/></svg>
    <span>Elmfield Gardens, Northbay Northbay<br>NB4 2 United Kingdom</span>
  </div>
  <div class="strip-item" style="left:585px;top:12px">
    <span style="width:20px"><svg width="18" height="16" viewBox="0 0 24 24"><path d="M6.6 10.8a15 15 0 0 0 6.6 6.6l2.2-2.2a1 1 0 0 1 1-.25 11.4 11.4 0 0 0 3.6.57 1 1 0 0 1 1 1V20a1 1 0 0 1-1 1A17 17 0 0 1 3 4a1 1 0 0 1 1-1h3.5a1 1 0 0 1 1 1 11.4 11.4 0 0 0 .57 3.6 1 1 0 0 1-.25 1z" fill="none" stroke="#EE7325" stroke-width="2"/></svg><br><svg width="18" height="14" viewBox="0 0 18 14"><rect x="1" y="1" width="16" height="12" fill="#EE7325"/><path d="M1 1l8 7 8-7" fill="none" stroke="#fff" stroke-width="1.4"/></svg></span>
    <span>07700900418<br>sales@trellanstaffing.example.com</span>
  </div>
</div>

<div class="role-card abs" style="left:161px;background:linear-gradient(180deg,#c9d2de,#6f87b0)" role="img" aria-label="Nurse in blue scrubs with a stethoscope"><span>NURSE</span></div>
<div class="role-card abs" style="left:386px;background:linear-gradient(180deg,#c7cbd0,#7f9fc0)" role="img" aria-label="Group of staff nurses in light blue uniforms"><span>STAFF NURSE</span></div>
<div class="role-card abs" style="left:611px;background:linear-gradient(180deg,#d8d9d6,#8a8f90)" role="img" aria-label="Engineer in a yellow hard hat"><span>ENGINEER</span></div>
<div class="role-card abs" style="left:837px;background:linear-gradient(180deg,#8a8c88,#5b5f5c)" role="img" aria-label="Welder in a white hard hat and overalls"><span>WELDER</span></div>

<h2 class="section-title abs centered" style="top:1482px">WORKING TOGETHER</h2>
<p class="intro abs centered" style="top:1552px;font-size:13px">We recruit the finest talent available with our dedicated 200 strong team.<br>Our centres are highlighted in <span style="color:var(--red)">Red Dots</span> on the map.</p>
<div class="ph" style="left:332px;top:1616px;width:542px;height:306px;background:radial-gradient(ellipse at 50% 55%,#cfe2f3 0%,#eaf2fa 55%,#fff 80%)" role="img" aria-label="Map of the Philippines with red markers at Baguio, Manila, Batangas, Bacolod and Davao"></div>

<section class="band abs">
  <div class="ph" style="left:0;top:99px;width:559px;height:335px;background:linear-gradient(120deg,#e9eef3,#b9c8d8)" role="img" aria-label="Two businessmen working together at a computer with UK and Philippine flags on the desk"></div>
  <h2 class="section-title abs" style="left:646px;top:113px">WHAT WE DO</h2>
  <div class="rule abs" style="left:646px;top:167px"></div>
  <p class="body-copy abs" style="left:646px;top:182px;width:395px">Our company has been estabilished in the Philippines for over 20 years. We have mainly been recruiting philippine workers for the off shore industry in asia but since brexit and the new rules on skilled workers entering the UK we have been working with UK companies who now have chance to recruit some of the finest hard working talent from the Philippines for their companies..</p>
  <span class="btn abs" style="left:646px;top:376px">Contact Us Today</span>
</section>

<h2 class="section-title abs" style="left:163px;top:2688px">HOW WE HELP</h2>
<div class="rule abs" style="left:163px;top:2742px"></div>
<p class="body-copy abs" style="left:163px;top:2760px;width:385px">We work with companies to find skilled workers that meet the UK requirements for Visas and work permits. We guide you through the whole process and deliver highly trained people that add value to your business. We are here to help both the companies and the Philippino people to gain a better standard of living for their families.</p>
<div class="ph" style="left:673px;top:2638px;width:527px;height:346px;background:linear-gradient(110deg,#3a3f46,#d8dadc)" role="img" aria-label="Two businessmen in suits shaking hands over a signed contract"></div>

<section class="panel abs" style="left:0;background:linear-gradient(135deg,#d7e5f2,#c2d8ec)">
  <h2 class="section-title" style="margin-top:124px">WHERE TO START</h2>
  <div class="rule" style="margin:14px auto 0;background:#fff"></div>
  <p style="margin-top:14px;width:540px">We need to know what your issues are and how we can understand the personnal you require, over what time frame and the number of employees you need. Once this is estabilished we start sourcing workers in the Philippines that meet your criteria while starting the process in the UK to be able to have all the documents in place to deliver your company hard working skilled individuals.</p>
</section>
<section class="panel abs" style="left:600px;background:linear-gradient(135deg,#fbf3ec,#f5ebe2)">
  <h2 class="section-title" style="margin-top:124px">CONTACT US TODAY</h2>
  <div class="rule" style="margin:14px auto 0"></div>
  <p style="margin-top:14px;width:480px">Please contact us today with your requirements, this can be care workers, chef, welders, pipe fitters, caravan cabinet makers, medical workers. The UK list of required skills is extensive and the Philippines offersenglish speaking highly qualified hard working employees. Contact us today and make that first step to a highly motivated , quality skilled workforce.</p>
</section>

<div class="svc abs" style="left:161px">
  <div class="svc-icon"><svg width="50" height="50" viewBox="0 0 50 50" fill="none" stroke="#fff" stroke-width="2"><rect x="10" y="8" width="26" height="34" rx="2"/><path d="M16 18h14M16 25h14M16 32h9"/><circle cx="37" cy="33" r="6"/><path d="M41 37l5 5"/></svg></div>
  <h4>UK SKILLED WORKERS LIST</h4>
  <p>The UK government since brexit have developed a new system based on points...</p>
  <div class="more">Read More</div>
</div>
<div class="svc abs active" style="left:465px">
  <div class="svc-icon" style="background:var(--orange)"><svg width="50" height="50" viewBox="0 0 50 50" fill="none" stroke="#fff" stroke-width="2"><rect x="10" y="6" width="30" height="38" rx="2"/><path d="M16 16h18M16 23h18M16 30h10"/><circle cx="33" cy="35" r="5"/></svg></div>
  <h4>SPONSOR LICENCE</h4>
  <p>If you have areas of your business that meet the entry requirements of skilled labour...</p>
  <div class="more">Read More</div>
</div>
<div class="svc abs" style="left:769px">
  <div class="svc-icon"><svg width="50" height="50" viewBox="0 0 50 50" fill="none" stroke="#fff" stroke-width="2"><circle cx="18" cy="13" r="5"/><path d="M10 40V26a8 8 0 0 1 16 0v14"/><circle cx="35" cy="32" r="9"/><path d="M35 27v5l3 3"/></svg></div>
  <h4>RECRUITMENT TIMELINE</h4>
  <p>Brief us on the job profiles-this is passed on to our teams in the Philippines.</p>
  <div class="more">Read More</div>
</div>

<footer class="footer abs">
  <div class="abs" style="left:161px;top:118px;font-weight:600;font-size:22px">Trellan Staffing</div>
  <div class="social" style="left:163px"></div>
  <div class="social" style="left:201px"></div>
  <div class="social" style="left:239px"></div>
  <div class="social" style="left:277px"></div>

  <h5 style="left:441px;top:106px">QUICK LINKS</h5>
  <div class="link" style="left:441px;top:140px">› Home</div>
  <div class="link" style="left:441px;top:177px">› About</div>
  <div class="link" style="left:441px;top:214px">› Services</div>
  <div class="link" style="left:577px;top:140px">› Articles</div>
  <div class="link" style="left:577px;top:177px">› Training</div>
  <div class="link" style="left:577px;top:214px">› Contact Us</div>

  <h5 style="left:749px;top:106px">CONTACT DETAILS</h5>
  <div class="fline" style="left:749px;top:138px"><svg width="14" height="18" viewBox="0 0 14 18"><path d="M7 0a7 7 0 0 0-7 7c0 5 7 11 7 11s7-6 7-11a7 7 0 0 0-7-7z" fill="#fff"/><circle cx="7" cy="7" r="2.6" fill="#0B1A38"/></svg><span>Elmfield Gardens, Northbay Northbay<br>NB4 2 United Kingdom</span></div>
  <div class="fline" style="left:749px;top:186px"><svg width="16" height="16" viewBox="0 0 24 24"><path d="M6.6 10.8a15 15 0 0 0 6.6 6.6l2.2-2.2a1 1 0 0 1 1-.25 11.4 11.4 0 0 0 3.6.57 1 1 0 0 1 1 1V20a1 1 0 0 1-1 1A17 17 0 0 1 3 4a1 1 0 0 1 1-1h3.5a1 1 0 0 1 1 1 11.4 11.4 0 0 0 .57 3.6 1 1 0 0 1-.25 1z" fill="none" stroke="#fff" stroke-width="2"/></svg><span>07700900418</span></div>
  <div class="fline" style="left:749px;top:214px"><svg width="16" height="13" viewBox="0 0 18 14"><rect x="1" y="1" width="16" height="12" fill="#fff"/><path d="M1 1l8 7 8-7" fill="none" stroke="#0B1A38" stroke-width="1.4"/></svg><span>sales@trellanstaffing.example.com</span></div>

  <div class="copy">© 2023 Trellan Staffing Ltd. All Rights Reserved</div>
</footer>

</body>
</html>
```